RWT Fittings Ltd Business Cards

We need a business card with our business logo. We provide window and door installations on high-rises in west coast British Colombia, Canada.

I would like my business information and details on one side of the card, and the other side the company name with logo

Target Market(s)

General Contractors

Industry/Entity Type

Construction

Contact Information for Business Card

one side i want my company name and logo in the dark theme logo that i provided

Requirements
Must have
• Marco Peltieri, 16045518293, RWTFittings@mailbox-demo.com, 1407-5194 Linden Row Burnaby BC, V5H 2K9, Owner & Manager

```html
<!DOCTYPE html>
<html lang="en">
<head>
<meta charset="utf-8">
<title>RWT Fittings Ltd — Business Card</title>
<link rel="stylesheet" href="https://fonts.googleapis.com/css2?family=Open+Sans:wght@400;600;700&display=swap">
<style>
  :root {
    --stage: #3a3a3a;
    --card-white: #ffffff;
    --card-black: #111111;
    --pattern-dark: #1c1c1c;
    --pattern-mid: #262626;
    --brand-blue: #2a9fe0;
    --ink: #2b2b2b;
    --muted: #8a8a8a;
  }
  * { box-sizing: border-box; margin: 0; padding: 0; }
  html, body {
    width: 1200px; height: 780px; overflow: hidden;
    background: var(--stage);
    font-family: "Open Sans", sans-serif;
  }
  .sheet {
    width: 1200px; height: 780px;
    display: flex; align-items: center; justify-content: center; gap: 40px;
  }
  .card {
    position: relative;
    width: 540px; height: 310px;
    border-radius: 4px;
    overflow: hidden;
    box-shadow: 0 10px 30px rgba(0,0,0,.45);
  }

  /* Front */
  .card-front { background: var(--card-white); color: var(--ink); }
  .brand {
    position: absolute; left: 30px; top: 0; bottom: 0; width: 200px;
    display: flex; align-items: center; gap: 10px;
  }
  .brand-mark { width: 22px; height: 22px; background: var(--brand-blue); flex: none; }
  .brand-name {
    font-weight: 700; font-size: 20px; line-height: 1.1;
    color: var(--brand-blue); white-space: nowrap;
  }
  .divider {
    position: absolute; left: 232px; top: 40px; bottom: 40px;
    width: 1.5px; background: var(--brand-blue);
  }
  .details { position: absolute; left: 256px; top: 36px; right: 20px; }
  .person-name {
    font-weight: 700; font-size: 20px; letter-spacing: .3px;
    color: var(--brand-blue); text-transform: uppercase;
  }
  .person-role { font-size: 14px; margin-top: 1px; margin-bottom: 12px; }
  .contact-list { list-style: none; }
  .contact-item {
    display: flex; align-items: flex-start; gap: 8px;
    font-size: 12.5px; line-height: 1.35; margin-bottom: 5px;
  }
  .contact-item.address { margin-top: 8px; }
  .contact-icon { width: 16px; height: 16px; flex: none; margin-top: 1px; }
  .social {
    position: absolute; left: 256px; bottom: 26px;
    display: flex; align-items: center; gap: 10px;
  }
  .social-label { font-weight: 600; font-size: 18px; margin-right: 4px; }
  .social-dot { width: 16px; height: 16px; border-radius: 50%; background: var(--brand-blue); }

  /* Back */
  .card-back { background: var(--card-black); }
  .back-pattern {
    position: absolute; inset: 0;
    background: linear-gradient(135deg, var(--pattern-mid) 0%, var(--pattern-dark) 55%, var(--card-black) 100%);
  }
  .back-brand {
    position: absolute; inset: 0;
    display: flex; align-items: center; justify-content: center; gap: 12px;
  }
  .back-brand .brand-name { font-size: 28px; }
  .back-brand .brand-mark { width: 28px; height: 28px; }
</style>
</head>
<body>
<main class="sheet">

  <section class="card card-front" aria-label="Business card, front">
    <div class="brand">
      <span class="brand-mark"></span>
      <span class="brand-name">RWT Fittings Ltd</span>
    </div>

    <div class="divider"></div>

    <div class="details">
      <h1 class="person-name">Marco Peltieri</h1>
      <p class="person-role">Owner &amp; Manager</p>
      <ul class="contact-list">
        <li class="contact-item">
          <svg class="contact-icon" viewBox="0 0 16 16" aria-hidden="true">
            <circle cx="8" cy="8" r="8" fill="var(--brand-blue)"/>
            <path d="M5.2 4.2l1.4-.3.8 1.9-.9.7a5 5 0 0 0 2.9 2.9l.7-.9 1.9.8-.3 1.4c-3.7.2-6.7-2.8-6.5-6.5z" fill="#fff"/>
          </svg>
          <span>16045518293</span>
        </li>
        <li class="contact-item">
          <svg class="contact-icon" viewBox="0 0 16 16" aria-hidden="true">
            <circle cx="8" cy="8" r="8" fill="var(--brand-blue)"/>
            <rect x="4" y="5.2" width="8" height="5.6" fill="none" stroke="#fff" stroke-width="1"/>
            <path d="M4 5.4l4 3 4-3" fill="none" stroke="#fff" stroke-width="1"/>
          </svg>
          <span>RWTFittings@mailbox-demo.com</span>
        </li>
        <li class="contact-item">
          <svg class="contact-icon" viewBox="0 0 16 16" aria-hidden="true">
            <circle cx="8" cy="8" r="8" fill="var(--brand-blue)"/>
            <circle cx="8" cy="8" r="4" fill="none" stroke="#fff" stroke-width="1"/>
            <path d="M4 8h8M8 4c-1.6 2.2-1.6 5.8 0 8M8 4c1.6 2.2 1.6 5.8 0 8" fill="none" stroke="#fff" stroke-width=".9"/>
          </svg>
          <span>www.rwtfittings-demo.com</span>
        </li>
        <li class="contact-item address">
          <svg class="contact-icon" viewBox="0 0 16 16" aria-hidden="true">
            <circle cx="8" cy="8" r="8" fill="var(--brand-blue)"/>
            <path d="M8 12.5s-3-3.2-3-5.3a3 3 0 0 1 6 0c0 2.1-3 5.3-3 5.3z" fill="#fff"/>
            <circle cx="8" cy="7.2" r="1.1" fill="var(--brand-blue)"/>
          </svg>
          <span>1407-5194 Linden Row<br>Burnaby BC, V5H 2K9</span>
        </li>
      </ul>
    </div>

    <div class="social">
      <span class="social-label">Follow Us</span>
      <span class="social-dot"></span>
      <span class="social-dot"></span>
      <span class="social-dot"></span>
    </div>
  </section>

  <section class="card card-back" aria-label="Business card, back">
    <div class="back-pattern" role="img" aria-label="Tone-on-tone repeating pattern of dark building silhouettes"></div>
    <div class="back-brand">
      <span class="brand-mark"></span>
      <span class="brand-name">RWT Fittings Ltd</span>
    </div>
  </section>

</main>
</body>
</html>
```